Banner ads for LP that work with same theme as below banners

Love the banner ads below. Need more with attached photos. But use the same wording, font as in below banner ads. Should be LP size 1200/627 so I can use for Pixorly and LP. Looking for great ads to use as LP ads. We do lots of ads so it will be worth your time to enter this contest you will be rewarded with a ton of work. Need several banner ads that work together. So maybe 1 of the dresses, 1 of the sweater, 1 of the leggings, 1 of the jacket

Target Market(s)

Women 24-45

Industry/Entity Type

Fashion

Requirements
Must have
• Banner ads that work for LP and Pixorly
Nice to have
• Several options to choose from
Should not have
• not sure

```html
<!DOCTYPE html>
<html lang="en">
<head>
<meta charset="UTF-8">
<title>Winter Wear Collection</title>
<link href="https://fonts.googleapis.com/css2?family=Great+Vibes&family=Playfair+Display:wght@400;700;900&display=swap" rel="stylesheet">
<style>
  :root {
    --night: #1b2840;
    --night-deep: #141d31;
    --glow-red: #c8333f;
    --glow-violet: #7a5d9e;
    --glow-amber: #d88a4a;
    --ivory: #ffffff;
    --crimson: #c8183f;
    --lace-light: #cfc4b8;
    --lace-dark: #141112;
  }
  html, body {
    margin: 0;
    padding: 0;
    width: 1200px;
    height: 627px;
    overflow: hidden;
    background: var(--night-deep);
  }
  .banner {
    position: relative;
    width: 1200px;
    height: 627px;
    overflow: hidden;
  }
  .city-lights {
    position: absolute;
    inset: 0;
    background:
      radial-gradient(circle at 78% 30%, rgba(216,138,74,0.35), transparent 30%),
      radial-gradient(circle at 62% 45%, rgba(200,51,63,0.35), transparent 28%),
      radial-gradient(circle at 90% 60%, rgba(200,51,63,0.3), transparent 30%),
      radial-gradient(circle at 8% 35%, rgba(255,255,255,0.22), transparent 18%),
      radial-gradient(circle at 95% 15%, rgba(122,93,158,0.35), transparent 25%),
      radial-gradient(circle at 30% 85%, rgba(122,93,158,0.3), transparent 30%),
      linear-gradient(160deg, var(--night) 0%, var(--night-deep) 100%);
  }
  .model {
    position: absolute;
    border-radius: 80px 80px 20px 20px;
  }
  .model--floral {
    left: 222px;
    top: 38px;
    width: 178px;
    height: 589px;
    background: linear-gradient(180deg, #6a4a3e 0%, var(--lace-light) 22%, #d9d2c8 70%, #bdb3a8 100%);
  }
  .model--lace {
    left: 402px;
    top: 32px;
    width: 172px;
    height: 595px;
    background: linear-gradient(180deg, #b58a5e 0%, #2a2224 24%, var(--lace-dark) 60%, #1e1a1c 100%);
  }
  .headline {
    position: absolute;
    left: 600px;
    top: 168px;
    width: 460px;
    text-align: center;
    color: var(--ivory);
  }
  .headline__script {
    display: block;
    font-family: "Great Vibes", cursive;
    font-size: 66px;
    line-height: 1;
    margin-left: 10px;
  }
  .headline__main {
    display: block;
    font-family: "Playfair Display", serif;
    font-weight: 700;
    font-size: 64px;
    letter-spacing: 5px;
    line-height: 1;
    margin-top: 8px;
  }
  .cta {
    position: absolute;
    left: 698px;
    top: 337px;
    width: 276px;
    height: 46px;
    background: var(--crimson);
    color: var(--ivory);
    display: flex;
    align-items: center;
    justify-content: center;
    gap: 7px;
    font-family: "Playfair Display", serif;
    font-size: 22px;
    letter-spacing: 2px;
    text-decoration: none;
  }
  .cta__strong { font-weight: 700; }
  .cta__light { font-weight: 400; font-size: 19px; }
</style>
</head>
<body>
  <div class="banner">
    <div class="city-lights" role="img" aria-label="Blurred night city street lights in red, amber and violet bokeh"></div>
    <div class="model model--floral" role="img" aria-label="Model in a sheer embroidered floral maxi dress"></div>
    <div class="model model--lace" role="img" aria-label="Model in a black lace handkerchief-hem dress with lace-up heels"></div>
    <h1 class="headline">
      <span class="headline__script">Winter Wear</span>
      <span class="headline__main">COLLECTION</span>
    </h1>
    <a class="cta" href="#">
      <span class="cta__strong">SHOP</span>
      <span class="cta__light">THE</span>
      <span class="cta__strong">LOOK</span>
    </a>
  </div>
</body>
</html>
```